A private security company called "Tavron Security Services Ltd"

Hello everybody,

We need a web page for a company based in NZ. It is mainly an informative website so it would be wonderful if the designer puts their absolute best into making it a website that I would really appreciate. The website needs to show professionalism and also needs to make our web surfers find the information they need in a click. the company's colour is black and silver, and if those two colours could be integrated into the website it would be absolutely lovely. Please do contact me for any information.

Sincerely,
Dorian Vaskel

Industry/Entity Type

Security

```html
<!DOCTYPE html>
<html lang="en">
<head>
<meta charset="utf-8">
<title>Tavron Security Services Ltd</title>
<link href="https://fonts.googleapis.com/css2?family=Encode+Sans+Condensed:wght@400;500;600&family=Arimo:wght@400;700&display=swap" rel="stylesheet">
<style>
:root{
  --black:#1c1c1c;
  --charcoal:#2e2e2e;
  --graphite:#3d3d3d;
  --silver:#d9d9d9;
  --silver-light:#ededed;
  --silver-mid:#bdbdbd;
  --ink:#1a1a1a;
  --text-grey:#8a8a8a;
  --line:#cfcfcf;
  --white:#ffffff;
  --footer-text:#8c8c8c;
}
*{margin:0;padding:0;box-sizing:border-box}
html,body{width:1200px;height:2619px;overflow:hidden}
body{position:relative;background:var(--white);font-family:"Arimo",Arial,sans-serif;color:var(--ink)}
.abs{position:absolute}
.head-font{font-family:"Encode Sans Condensed","Arial Narrow",sans-serif;font-weight:500}

/* header */
.site-header{left:0;top:0;width:1200px;height:159px;background:linear-gradient(#fdfdfd,#e6e6e6);border-bottom:2px solid #cfcfcf}
.brand{left:157px;top:38px;display:flex;align-items:center;gap:12px}
.brand-dot{width:40px;height:40px;border-radius:50%;background:var(--charcoal)}
.brand-name{font-family:"Encode Sans Condensed","Arial Narrow",sans-serif;font-weight:600;font-size:24px;line-height:26px;color:var(--ink);width:190px}
.main-nav{top:97px;left:405px;display:flex;gap:0}
.main-nav a{font-size:13.5px;color:var(--ink);text-decoration:none;text-transform:uppercase;margin-right:38px;letter-spacing:.2px}
.social{display:flex;gap:9px}
.social span{width:30px;height:30px;border-radius:50%;background:var(--silver-mid);display:block}
.social-top{left:934px;top:32px}

/* hero */
.hero{left:0;top:159px;width:1200px;height:515px;background:radial-gradient(ellipse at 60% 40%,#6a6a6a 0%,#4a4a4a 40%,#262626 100%)}
.hero-photo{left:595px;top:38px;width:453px;height:477px;background:linear-gradient(#5a5a5a,#1a1a1a 70%);border-radius:200px 200px 0 0}
.hero-title{left:180px;top:222px;color:var(--white);font-size:36px;line-height:46px;font-family:"Encode Sans Condensed","Arial Narrow",sans-serif;font-weight:400}
.hero-title b{font-weight:600;font-size:40px}
.slide-arrow{width:52px;height:52px;border-radius:50%;background:rgba(0,0,0,.45)}
.slide-arrow svg{width:52px;height:52px}
.hero .prev{left:101px;top:231px}
.hero .next{left:1047px;top:231px}

/* solutions */
.solution{width:300px;text-align:center}
.solution-img{width:184px;height:184px;border-radius:50%;margin:0 auto;border:8px solid #e4e4e4;box-shadow:0 0 0 1px #ccc}
.solution h3{margin-top:40px;font-size:20px;color:var(--ink)}
.solution p{margin:24px auto 0;width:250px;font-size:12.5px;line-height:17px;color:var(--text-grey)}
.btn-more{display:inline-block;border:1px solid #b5b5b5;border-radius:3px;background:linear-gradient(#fafafa,#dcdcdc);font-size:12px;color:var(--ink);padding:7px 0;width:112px;text-align:center}
.solution .btn-more{margin-top:22px}

/* services band */
.services-band{left:0;top:1133px;width:1200px;height:585px;background:linear-gradient(#e4e4e4,#f2f2f2 30%,#dadada)}
.side-title{left:157px;top:1164px;font-size:24px}
.side-list{left:157px;top:1220px;list-style:none}
.side-list li{height:37px;font-size:12.5px;color:#777;display:flex;align-items:center;gap:14px}
.side-list li i{width:14px;height:14px;border-radius:50%;background:#fff;border:1px solid #ccc;display:block;position:relative}
.side-list li i::after{content:"";position:absolute;left:3px;top:3px;width:4px;height:4px;border-right:1.5px solid #555;border-top:1.5px solid #555;transform:rotate(45deg)}
.promo{left:157px;top:1557px;width:214px;height:150px;background:linear-gradient(90deg,#5d5d5d,#9a9a9a 60%,#c4c4c4)}
.promo p{position:absolute;left:14px;top:14px;color:var(--white);font-size:24px;line-height:30px;font-family:"Encode Sans Condensed","Arial Narrow",sans-serif;text-transform:uppercase}
.promo p small{display:block;font-size:20px;margin-top:4px}
.service-col{border-left:1px solid var(--line)}
.service{position:absolute;background:linear-gradient(#f7f7f7,#ececec);border-bottom:1px solid var(--line);padding:18px 18px 0}
.service h4{font-size:19px;margin-bottom:22px}
.service p{font-size:11.5px;line-height:17px;color:#8b8b8b;letter-spacing:.3px}
.service p+p{margin-top:12px}
.service .btn-more{position:absolute;right:16px;width:70px;font-size:11px;padding:5px 0}

/* industries */
.industries-title{left:0;width:1200px;top:1776px;text-align:center;font-size:40px}
.industry{width:195px;text-align:center}
.industry-img{width:195px;height:157px;border:5px solid #e5e5e5}
.industry p{margin-top:16px;font-size:19px}
.ind-arrow{width:34px;height:34px;border-radius:50%;background:#bdbdbd}
.ind-arrow svg{width:34px;height:34px}

/* footer */
.site-footer{left:0;top:2140px;width:1200px;height:397px;background:linear-gradient(#2b2b2b,#444 45%,#3a3a3a)}
.footer-bar{left:0;top:2537px;width:1200px;height:82px;background:#3b3b3b;border-top:1px solid #2a2a2a}
.f-title{color:var(--white);font-size:28px}
.f-text{color:var(--footer-text);font-size:12px;line-height:15.5px}
.quick-links{list-style:none}
.quick-links li{height:31px;font-size:12.5px;color:var(--footer-text);display:flex;align-items:center;gap:14px;text-transform:uppercase}
.quick-links li::before{content:"";width:6px;height:6px;border-right:2px solid #ddd;border-top:2px solid #ddd;transform:rotate(45deg)}
.field{width:275px;height:34px;background:#6a6a6a;border:1px solid #777;color:#d0d0d0;font-size:12.5px;padding:9px 20px}
.signup{width:144px;height:35px;background:linear-gradient(#fff,#dcdcdc);border:1px solid #aaa;border-radius:2px;font-size:12.5px;text-align:center;line-height:33px;color:var(--ink)}
.copyright{left:157px;top:2572px;color:#999;font-size:12.5px}
.social-bottom{left:934px;top:2563px}
.social-bottom span{background:#777}
</style>
</head>
<body>

<header class="abs site-header">
  <div class="abs brand"><span class="brand-dot"></span><span class="brand-name">Tavron Security Services Ltd.</span></div>
  <div class="abs social social-top"><span></span><span></span><span></span></div>
  <nav class="abs main-nav">
    <a>Home</a><a>Our Services</a><a>About</a><a>Locations</a><a>News</a><a>Careers</a><a>Contact Us</a>
  </nav>
</header>

<section class="abs hero">
  <div class="abs hero-photo" role="img" aria-label="Photo of a security officer in dark glasses and headset, arms crossed, wearing a black security shirt"></div>
  <div class="abs slide-arrow prev"><svg viewBox="0 0 52 52"><path d="M30 15 L20 26 L30 37" fill="none" stroke="#fff" stroke-width="2.5"/></svg></div>
  <div class="abs slide-arrow next"><svg viewBox="0 0 52 52"><path d="M22 15 L32 26 L22 37" fill="none" stroke="#fff" stroke-width="2.5"/></svg></div>
  <h1 class="abs hero-title"><b>Lorem Ipsum</b> is simply dummy text of<br>the printing and typesetting industry.</h1>
</section>

<section class="solutions">
  <div class="abs solution" style="left:123px;top:722px">
    <div class="solution-img" role="img" aria-label="Photo of a woman using a home alarm keypad" style="background:linear-gradient(135deg,#c9b59a,#7b6a57)"></div>
    <h3 class="head-font">Residential Solutions</h3>
    <p>Lorem ipsum dolor sit amet, consec tetur adipiscing elit. Donec vitae pharetra nunc. Aliquam condimentum neque nibh, ac vestibulum</p>
    <span class="btn-more">Read More</span>
  </div>
  <div class="abs solution" style="left:449px;top:722px">
    <div class="solution-img" role="img" aria-label="Photo of a uniformed guard in front of an office tower" style="background:linear-gradient(135deg,#9fb6cc,#2b3440)"></div>
    <h3 class="head-font">Commercial Solutions</h3>
    <p>Lorem ipsum dolor sit amet, consec tetur adipiscing elit. Donec vitae pharetra nunc. Aliquam condimentum neque nibh, ac vestibulum</p>
    <span class="btn-more">Read More</span>
  </div>
  <div class="abs solution" style="left:775px;top:722px">
    <div class="solution-img" role="img" aria-label="Photo of operators in a CCTV control room" style="background:linear-gradient(135deg,#5b86b8,#1d2f45)"></div>
    <h3 class="head-font">Technology Solutions</h3>
    <p>Lorem ipsum dolor sit amet, consec tetur adipiscing elit. Donec vitae pharetra nunc. Aliquam condimentum neque nibh, ac vestibulum</p>
    <span class="btn-more">Read More</span>
  </div>
</section>

<section class="abs services-band"></section>
<h2 class="abs head-font side-title">Services</h2>
<ul class="abs side-list">
  <li><i></i>Access Control</li><li><i></i>Video Surveillance</li><li><i></i>Intrusion Detection</li>
  <li><i></i>Locking Solutions</li><li><i></i>Key Control</li><li><i></i>Security Guard</li>
  <li><i></i>Security Patrol</li><li><i></i>Alarm Monitoring</li><li><i></i>Executive Protection</li>
</ul>
<div class="abs promo" role="img" aria-label="Photo of a guard at a doorway, custom options banner">
  <p>Custom<br>Options<br>Available<small>Call 555-0142-77</small></p>
</div>

<div class="abs service-col" style="left:376px;top:1133px;height:585px"></div>
<div class="abs service-col" style="left:599px;top:1133px;height:585px"></div>
<div class="abs service-col" style="left:822px;top:1133px;height:585px"></div>
<div class="abs service-col" style="left:1045px;top:1133px;height:585px"></div>

<article class="service" style="left:377px;top:1145px;width:221px;height:265px">
  <h4 class="head-font">Access Control</h4>
  <p>Lorem ipsum dolor sit amet, cons ectetuer adipiscing elit, sed diam nonummy nibh euismod tincidunt</p>
  <p>ut laoreet dolore magna aliquam erat volutpat. Ut wisi enim ad min im veniam, quis nostrud exerci ta tion ullamcorper suscipit lobortis nisl.</p>
  <span class="btn-more" style="top:222px">Read More</span>
</article>
<article class="service" style="left:377px;top:1410px;width:221px;height:308px;border-bottom:0">
  <h4 class="head-font" style="margin-top:24px">Security Guard</h4>
  <p>Lorem ipsum dolor sit amet, cons ectetuer adipiscing elit, sed diam nonummy nibh euismod tincidunt ut laoreet dolore magna aliquam erat volutpat. Ut wisi enim ad mini m veniam, quis nostrud exerci tati on ullamcorper suscipit lobortis n isl ut aliquip ex ea commodo cons equat.</p>
  <span class="btn-more" style="top:230px">Read More</span>
</article>

<article class="service" style="left:600px;top:1145px;width:221px;height:287px">
  <h4 class="head-font">Video Surveillance</h4>
  <p>Duis autem vel eum iriure dolor i n hendrerit in vulputate velit esse molestie consequat.</p>
  <p>Vel illum dolore eu feugiat nulla f acilisis at vero eros et accumsan et iusto odio dignissim qui bland t praesent luptatum zzril delenit a ugue duis dolore te feugait nulla facilisi.</p>
  <span class="btn-more" style="top:244px">Read More</span>
</article>
<article class="service" style="left:600px;top:1432px;width:221px;height:286px;border-bottom:0">
  <h4 class="head-font" style="margin-top:20px">Alarm Monitoring</h4>
  <p>Duis autem vel eum iriure dolor in hendrerit in vulputate velit ess e molestie consequat, vel illum d olore eu feugiat nulla facilisis at vero eros et accumsan et iusto o dio dignissim qui blandit praese nt luptatum zzril delenit augue du is dolore</p>
  <span class="btn-more" style="top:228px">Read More</span>
</article>

<article class="service" style="left:823px;top:1145px;width:221px;height:250px">
  <h4 class="head-font">Key Control</h4>
  <p>Ut wisi enim ad minim veniam, qu is nostrud exerci tation ullamcorp er suscipit lobortis nisl ut aliquip ex ea commodo consequat. Duis autem vel eum iriure dolor in hen drerit in vulputate velit.</p>
  <span class="btn-more" style="top:207px">Read More</span>
</article>
<article class="service" style="left:823px;top:1395px;width:221px;height:323px;border-bottom:0">
  <h4 class="head-font" style="margin-top:16px">Executive Protection</h4>
  <p>Lorem ipsum dolor sit amet, cons ectetuer adipiscing elit, sed diam nonummy nibh euismod tincidunt ut laoreet dolore magna aliquam erat volutpat. Ut wisi enim ad mini m veniam, quis nostrud exerci tati on ullamcorper suscipit lobortis n isl ut aliquip ex ea commodo cons equat.</p>
  <span class="btn-more" style="top:222px">Read More</span>
</article>

<h2 class="abs head-font industries-title">Industries We Serve</h2>
<div class="abs ind-arrow" style="left:109px;top:1949px"><svg viewBox="0 0 34 34"><path d="M20 10 L13 17 L20 24" fill="none" stroke="#fff" stroke-width="2"/></svg></div>
<div class="abs ind-arrow" style="left:1054px;top:1949px"><svg viewBox="0 0 34 34"><path d="M14 10 L21 17 L14 24" fill="none" stroke="#fff" stroke-width="2"/></svg></div>
<div class="abs industry" style="left:157px;top:1887px">
  <div class="industry-img" role="img" aria-label="Photo of a campus officer talking with students on a lawn" style="background:linear-gradient(#8fa879,#4e6a3d)"></div>
  <p class="head-font">Campus Security</p>
</div>
<div class="abs industry" style="left:388px;top:1887px">
  <div class="industry-img" role="img" aria-label="Photo of a guard on a patrol scooter in a shopping mall" style="background:linear-gradient(#b89d78,#6e5a44)"></div>
  <p class="head-font">Shoping Center</p>
</div>
<div class="abs industry" style="left:620px;top:1887px">
  <div class="industry-img" role="img" aria-label="Photo of CCTV cameras against an industrial skyline" style="background:linear-gradient(#e4eef4,#9bb3c4)"></div>
  <p class="head-font">Industrial Security</p>
</div>
<div class="abs industry" style="left:848px;top:1887px">
  <div class="industry-img" role="img" aria-label="Photo of an operator watching monitoring screens" style="background:linear-gradient(#6d5a52,#251d1a)"></div>
  <p class="head-font">Security Monitoring</p>
</div>

<footer class="abs site-footer"></footer>
<h3 class="abs head-font f-title" style="left:157px;top:2196px">About us</h3>
<div class="abs f-text" style="left:157px;top:2263px;width:304px">
  <p>Lorem ipsum dolor sit amet, consectetur adipiscing elit. Morbi pellentesque iaculis justo eget fermentum. Pellentesque commodo iaculis neque, vitae tincidun odio pellentesque luctus. Aenean in eros eu magna vestibulum imperdiet pretium nec augue</p>
  <p style="margin-top:15px">Etiam quis turpis enim. Vestibulum auctor id mauris vulputate consequat. Suspendisse potenti. Cras at imperdiet elit. Integer fringilla tellus non diam condimentum, sed ultricies urna ultricies. Sed cong dui quis dui convallis dictum. Donec malesuada vulputate risus vitae vulputate. Maecenas in congue urna. Sed porttitor bibendum</p>
</div>
<h3 class="abs head-font f-title" style="left:541px;top:2196px">Quick Links</h3>
<ul class="abs quick-links" style="left:541px;top:2256px">
  <li>Home</li><li>Our Services</li><li>About</li><li>Locations</li><li>News</li><li>Careers</li><li>Contact Us</li>
</ul>
<h3 class="abs head-font f-title" style="left:768px;top:2196px">Newsletter Sigup</h3>
<p class="abs f-text" style="left:768px;top:2263px;width:280px">Fill the form below and recive our latest offers &amp; updates</p>
<div class="abs field" style="left:768px;top:2333px">Your Name</div>
<div class="abs field" style="left:768px;top:2380px">Your Email</div>
<div class="abs signup" style="left:768px;top:2432px">Signup Now!</div>

<div class="abs footer-bar"></div>
<p class="abs copyright">Copyright © 2014 Tavron Security Service LTD.</p>
<div class="abs social social-bottom"><span></span><span></span><span></span></div>

</body>
</html>
```